Garlic Farm for Farm Sales/Restaurant sales

Need a professional, but appealing to agriculture world. We are selling 27 kinds of Organic Garlic from a farm in Simla,CO. I have uploaded logo and business information-we are going to need a template, because I will need to use it for four separate people.
-We are trying to appeal to Farm to table restaurants
-As well as growers/farmers

Target Market(s)

Agriculture Sales/Restaurants-Organic

Industry/Entity Type

Agriculture

Contact Information for Business Card

Want it to look more unique then your average kelto stock card- I want it to look amazing

Font styles to use
Sans Serif

Colors
0455a3
ec1f27
fbed22
ffffff

Requirements
Must have
• Just be creative
Nice to have
• Colorful
Should not have
• plain

```html
<!DOCTYPE html>
<html lang="en">
<head>
<meta charset="utf-8">
<title>Summit Ridge Garlic – Business Card</title>
<link rel="stylesheet" href="https://fonts.googleapis.com/css2?family=Josefin+Sans:wght@400;600;700&display=swap">
<style>
  :root {
    --navy: #1b3262;
    --red: #d0202e;
    --yellow: #f4e01c;
    --white: #ffffff;
    --stage: #e6e7ea;
    --ink-soft: #2a3c6e;
  }
  * { box-sizing: border-box; margin: 0; padding: 0; }
  html, body { width: 1200px; height: 900px; overflow: hidden; }
  body {
    background: var(--stage);
    font-family: "Josefin Sans", sans-serif;
    position: relative;
  }
  .card {
    position: absolute;
    left: 250px;
    width: 700px;
    height: 400px;
    overflow: hidden;
    box-shadow: 0 6px 18px rgba(0,0,0,0.18);
  }
  .card-front { top: 30px; background: var(--navy); }
  .card-back { top: 470px; background: var(--white); }

  /* shared stripe system */
  .stripe { position: absolute; background: var(--red); }
  .bar {
    position: absolute;
    border-radius: 8px;
  }

  /* front */
  .front-brand {
    position: absolute;
    left: 0; right: 0; top: 80px;
    display: flex; flex-direction: column; align-items: center; gap: 18px;
  }
  .brand-dot {
    width: 96px; height: 96px; border-radius: 50%;
    background: var(--red);
  }
  .brand-name {
    color: var(--white);
    font-weight: 600;
    font-size: 34px;
    letter-spacing: 1px;
    text-transform: lowercase;
  }
  .social-row {
    position: absolute;
    top: 272px; left: 0; right: 0;
    display: flex; justify-content: center; gap: 14px;
  }
  .social-dot {
    width: 20px; height: 20px; border-radius: 50%;
    background: var(--red);
  }
  .card-front .stripe-right { right: 0; top: 236px; width: 130px; height: 22px; }
  .card-front .bar-main { left: 300px; top: 258px; width: 290px; height: 0; }
  .card-front .bar-low {
    background: var(--white);
    left: 290px; top: 318px; width: 300px; height: 22px;
  }
  .card-front .stripe-left { left: 0; top: 340px; width: 300px; height: 24px; }
  .card-front .stripe-right2 { right: 0; top: 296px; width: 120px; height: 22px; }

  /* back */
  .back-brand {
    position: absolute;
    left: 70px; top: 95px; width: 210px;
    display: flex; flex-direction: column; align-items: center; gap: 12px;
  }
  .back-brand .brand-dot { width: 130px; height: 130px; }
  .back-brand .brand-name { color: var(--navy); font-size: 17px; letter-spacing: 0.5px; }
  .divider {
    position: absolute;
    left: 312px; top: 80px;
    width: 2px; height: 150px;
    background: var(--yellow);
  }
  .contact {
    position: absolute;
    left: 340px; top: 95px;
  }
  .person-name {
    font-size: 30px; font-weight: 700; letter-spacing: 1.5px;
    text-transform: uppercase; color: var(--navy);
    margin-bottom: 14px;
  }
  .person-name .surname { color: var(--red); }
  .contact-list { list-style: none; }
  .contact-item {
    display: flex; align-items: center; gap: 12px;
    font-size: 17px; color: var(--ink-soft);
    margin-bottom: 8px;
  }
  .contact-item .accent { color: var(--red); }
  .contact-icon {
    width: 17px; height: 17px; border-radius: 3px;
    background: var(--red);
    display: flex; align-items: center; justify-content: center;
    flex: none;
  }
  .card-back .stripe-right { right: 0; top: 232px; width: 150px; height: 22px; }
  .card-back .bar-address {
    background: var(--navy);
    left: 260px; top: 254px; width: 300px; height: 26px;
    display: none;
  }
  .card-back .stripe-right2 { right: 0; top: 268px; width: 0; height: 0; }
  .card-back .address-bar {
    position: absolute;
    background: var(--navy);
    border-radius: 8px;
    left: 250px; top: 300px; width: 320px; height: 30px;
    color: var(--white);
    font-size: 16px; letter-spacing: 0.5px;
    display: flex; align-items: center; justify-content: center;
  }
  .card-back .stripe-left { left: 0; top: 344px; width: 260px; height: 22px; }
  .card-back .stripe-right { top: 278px; }
</style>
</head>
<body>

<section class="card card-front" aria-label="Card front">
  <div class="front-brand">
    <div class="brand-dot"></div>
    <div class="brand-name">summit ridge garlic</div>
  </div>
  <div class="social-row" aria-label="Social links">
    <span class="social-dot"></span>
    <span class="social-dot"></span>
    <span class="social-dot"></span>
    <span class="social-dot"></span>
  </div>
  <div class="stripe stripe-right2"></div>
  <div class="bar bar-low"></div>
  <div class="stripe stripe-left"></div>
</section>

<section class="card card-back" aria-label="Card back">
  <div class="back-brand">
    <div class="brand-dot"></div>
    <div class="brand-name">summit ridge garlic</div>
  </div>
  <div class="divider"></div>
  <div class="contact">
    <h1 class="person-name">Dana <span class="surname">Whitlow</span></h1>
    <ul class="contact-list">
      <li class="contact-item">
        <span class="contact-icon">
          <svg width="11" height="11" viewBox="0 0 24 24"><path fill="#fff" d="M6.6 10.8a15 15 0 006.6 6.6l2.2-2.2c.3-.3.7-.4 1-.2 1.1.4 2.3.6 3.6.6.6 0 1 .4 1 1V20c0 .6-.4 1-1 1A17 17 0 013 4c0-.6.4-1 1-1h3.5c.6 0 1 .4 1 1 0 1.3.2 2.5.6 3.6.1.3 0 .7-.2 1z"/></svg>
        </span>
        555-014-2290
      </li>
      <li class="contact-item">
        <span class="contact-icon">
          <svg width="11" height="11" viewBox="0 0 24 24"><path fill="#fff" d="M3 5h18v14H3z"/><path fill="none" stroke="#d0202e" stroke-width="2" d="M3 6l9 7 9-7"/></svg>
        </span>
        Dana@SRGarlic.com
      </li>
      <li class="contact-item">
        <span class="contact-icon">
          <svg width="11" height="11" viewBox="0 0 24 24"><circle cx="12" cy="12" r="9" fill="none" stroke="#fff" stroke-width="2"/><path d="M3 12h18M12 3c3 3 3 15 0 18M12 3c-3 3-3 15 0 18" fill="none" stroke="#fff" stroke-width="1.6"/></svg>
        </span>
        www.<span class="accent">SRGarlic</span>.com
      </li>
    </ul>
  </div>
  <div class="stripe stripe-right"></div>
  <div class="address-bar">P.O. Box 12 Ridgeton, CO 80000</div>
  <div class="stripe stripe-left"></div>
</section>

</body>
</html>
```